Heritage Hollow Business Cards

Require a business card design. <br/><br/>Needs to include logo (either round or long version) plus these details:<br/>Maya Torvell<br/>Heritage Hollow<br/>maya@kelvadtrading.com.au<br/>02 6481 7395<br/>PO Box Glenwarra NSW 2791<br/>www.heritagehollow.com.au<br/><br/>I need in an editable format so that I can create for multiple staff members. <br/><br/>

Target Market(s)

We are an online store selling renovation products to home owners are builders. Looking for a classic classy design.

Industry/Entity Type

Home And Garden

Contact Information for Business Card

Maya Torvell
Heritage Hollow
maya@kelvadtrading.com.au
02 6481 7395
PO Box Glenwarra NSW 2791
www.heritagehollow.com.au

Colors

Designer to choose colors to be used in the design.

Requirements
Must have
• Must include Logo.

```html
<!DOCTYPE html>
<html lang="en">
<head>
<meta charset="utf-8">
<title>Heritage Hollow Business Cards</title>
<link href="https://fonts.googleapis.com/css2?family=Lora:wght@400;500&display=swap" rel="stylesheet">
<style>
  :root {
    --page-bg: #e9e7e4;
    --card-light: #ffffff;
    --card-dark: #231f20;
    --ink: #231f20;
    --ink-soft: #2e2a2b;
    --paper: #ffffff;
  }
  * { box-sizing: border-box; margin: 0; padding: 0; }
  html, body {
    width: 1189px; height: 1200px; overflow: hidden;
    background: var(--page-bg);
    font-family: "Lora", Georgia, serif;
  }
  .canvas { position: relative; width: 1189px; height: 1200px; }
  .card {
    position: absolute; left: 94px; width: 1000px; height: 556px;
    border-radius: 36px;
    box-shadow: 0 6px 18px rgba(0,0,0,0.18);
  }
  .card--front { top: 24px; background: var(--card-light); color: var(--ink); }
  .card--back { top: 620px; background: var(--card-dark); color: var(--paper); }

  .brand-name {
    position: absolute; font-weight: 500; font-size: 62px; line-height: 1;
    letter-spacing: 0.5px; white-space: nowrap;
  }
  .card--front .brand-name { left: 106px; top: 162px; color: var(--ink); }
  .card--back .brand-name { left: 0; right: 0; top: 296px; text-align: center; color: var(--paper); }

  .person { position: absolute; left: 61px; top: 300px; }
  .person__name { font-size: 32px; font-weight: 500; line-height: 1.1; }
  .person__title { font-size: 24px; line-height: 1.5; color: var(--ink-soft); }

  .divider {
    position: absolute; left: 61px; width: 872px; top: 393px;
    height: 2px; background: var(--ink);
  }

  .contact { position: absolute; left: 61px; top: 418px; list-style: none; }
  .contact li {
    display: flex; align-items: center; gap: 10px;
    height: 34px; font-size: 24px; color: var(--ink-soft);
  }
  .contact svg { width: 28px; height: 28px; flex: none; }

  .address {
    position: absolute; right: 67px; top: 418px; text-align: right;
    font-size: 24px; line-height: 34px; color: var(--ink-soft);
  }
</style>
</head>
<body>
<main class="canvas">
  <section class="card card--front" aria-label="Business card front">
    <h1 class="brand-name">Heritage Hollow</h1>

    <div class="person">
      <p class="person__name">Maya Torvell</p>
      <p class="person__title">Managing Director</p>
    </div>

    <div class="divider"></div>

    <ul class="contact">
      <li>
        <svg viewBox="0 0 28 28" aria-hidden="true">
          <circle cx="14" cy="14" r="12.5" fill="none" stroke="#231f20" stroke-width="1.6"/>
          <path d="M10.5 7.5 L12.5 7.5 L13.3 11 L11.8 12.2 C12.6 14.3 13.8 15.6 15.8 16.4 L17 15 L20.5 15.8 L20.5 17.8 C20.5 19 19.5 20 18.2 19.8 C13.2 19 9 14.8 8.3 9.8 C8.1 8.5 9.2 7.5 10.5 7.5 Z" fill="#231f20"/>
        </svg>
        <span>02 6481 7395</span>
      </li>
      <li>
        <svg viewBox="0 0 28 28" aria-hidden="true">
          <circle cx="14" cy="14" r="12.5" fill="none" stroke="#231f20" stroke-width="1.6"/>
          <rect x="7.5" y="9.5" width="13" height="9" rx="1" fill="#231f20"/>
          <path d="M8 10 L14 15 L20 10 M8 18 L12.5 13.8 M20 18 L15.5 13.8" fill="none" stroke="#fff" stroke-width="1"/>
        </svg>
        <span>maya@kelvadtrading.com.au</span>
      </li>
      <li>
        <svg viewBox="0 0 28 28" aria-hidden="true">
          <circle cx="14" cy="14" r="12.5" fill="none" stroke="#231f20" stroke-width="1.6"/>
          <circle cx="14" cy="14" r="7" fill="#231f20"/>
          <path d="M7 14 H21 M14 7 V21 M9 10.5 H19 M9 17.5 H19 M14 7 C10.5 10 10.5 18 14 21 M14 7 C17.5 10 17.5 18 14 21" fill="none" stroke="#fff" stroke-width="0.8"/>
        </svg>
        <span>www.heritagehollow.com.au</span>
      </li>
    </ul>

    <address class="address" style="font-style: normal;">
      PO Box Glenwarra<br>NSW 2791
    </address>
  </section>

  <section class="card card--back" aria-label="Business card back">
    <p class="brand-name">Heritage Hollow</p>
  </section>
</main>
</body>
</html>
```